Wordpress Template Design using existing Logo and Colors

We are wanting a wordpress theme designing for our b2b marketing consultancy business. A comprehesive and elagant design to our current site www.plovtrix.com would be good.

Industry/Entity Type

Marketing

Font styles to use
Sans Serif

```html
<!DOCTYPE html>
<html lang="en">
<head>
<meta charset="utf-8">
<title>Plovtrix — B2B Data &amp; Marketing Consulting</title>
<link rel="stylesheet" href="https://fonts.googleapis.com/css2?family=Lato:wght@400;700;900&display=swap">
<style>
:root{
  --red:#e4262a;
  --ink:#3e4758;
  --text:#4a4a4a;
  --band:#4f5a73;
  --white:#ffffff;
  --footer:#343434;
  --footer-deep:#262626;
  --footer-text:#d6d6d6;
}
*{box-sizing:border-box;margin:0;padding:0}
html,body{width:1200px;height:3141px;overflow:hidden;background:var(--white)}
body{font-family:"Lato",Arial,sans-serif;color:var(--text)}
.page{position:relative;width:1200px;height:3141px;overflow:hidden}
.abs{position:absolute}

/* header */
.site-header{left:0;top:0;width:1200px;height:121px;background:var(--white)}
.brand{left:75px;top:40px;display:flex;align-items:center;gap:10px}
.brand-name{font-weight:900;font-size:36px;letter-spacing:1px;color:var(--red)}
.brand-mark{width:14px;height:14px;background:var(--ink)}
.main-nav{right:73px;top:52px;display:flex;gap:45px;font-size:15px;color:var(--ink)}
.main-nav a{color:inherit;text-decoration:none}
.main-nav .is-active{color:var(--red)}

/* hero */
.hero{left:0;top:121px;width:1200px;height:545px}
.hero-photo{position:absolute;inset:0;background:linear-gradient(100deg,#3b3f44 0%,#8a8f96 35%,#c7b7a0 62%,#b5651f 100%)}
.hero-shade{position:absolute;inset:0;background:rgba(20,20,25,.28)}
.hero-copy{position:absolute;left:0;top:195px;width:1200px;text-align:center;color:var(--white)}
.hero-title{font-size:39px;font-weight:700;letter-spacing:.5px}
.hero-sub{margin-top:12px;font-size:18px;font-weight:700}
.hero .btn-solid{margin-top:22px}
.hero-dots{position:absolute;left:564px;top:502px;display:flex;gap:8px}
.hero-dots span{width:9px;height:9px;border-radius:50%;background:var(--white)}
.hero-dots .is-active{background:var(--red)}

/* buttons */
.btn-solid,.btn-outline{display:inline-block;height:44px;line-height:40px;padding:0 40px;font-size:14px;font-weight:700;text-transform:uppercase;text-decoration:none;text-align:center;min-width:178px}
.btn-solid{background:var(--red);color:var(--white);border:2px solid var(--white)}
.btn-outline{border:2px solid var(--red);color:var(--red)}
.btn-plain{border-color:var(--red)}

/* welcome */
.welcome{left:0;top:666px;width:1200px;height:318px;background:linear-gradient(#ffffff 40%,#f0f0f0 100%);text-align:center}
.welcome-title{margin-top:47px;font-size:30px;font-weight:700;color:var(--ink)}
.welcome-title em{font-style:normal;color:var(--red)}
.welcome-text{width:1000px;margin:28px auto 0;font-size:16px;line-height:28px;color:var(--text)}
.welcome .btn-outline{margin-top:28px}

/* feature rows */
.bands{left:0;top:0}
.feature-title{font-size:28px;font-weight:700;color:var(--ink);text-transform:uppercase}
.feature-text{margin-top:22px;font-size:16px;line-height:28px}
.feature-text.light,.feature-title.light{color:var(--white)}
.feature .btn-solid{margin-top:20px}
.art{position:absolute}

/* footer */
.site-footer{left:0;top:2733px;width:1200px;height:341px;background:var(--footer);color:var(--footer-text)}
.footer-col{position:absolute;top:50px;font-size:12.5px;line-height:18px}
.footer-heading{font-size:16px;font-weight:700;color:var(--white);margin-bottom:10px;text-transform:uppercase}
.footer-list{list-style:none}
.footer-list li{line-height:27px}
.contact-row{display:flex;gap:14px;margin-bottom:10px}
.contact-row svg{flex:none;margin-top:3px}
.footer-bar{left:0;top:3074px;width:1200px;height:67px;background:var(--footer-deep);color:#bdbdbd;font-size:11px}
.copyright{position:absolute;left:75px;top:28px}
.social{position:absolute;left:948px;top:24px;display:flex;gap:20px}
.social span{width:18px;height:18px;border-radius:50%;background:#d0d0d0}
</style>
</head>
<body>
<div class="page">

  <header class="site-header abs">
    <div class="brand abs"><span class="brand-name">PLOVTRIX</span><span class="brand-mark"></span></div>
    <nav class="main-nav abs">
      <a class="is-active" href="#">HOME</a>
      <a href="#">ABOUT</a>
      <a href="#">TARGET MARKETING</a>
      <a href="#">DATA MANAGEMENT</a>
      <a href="#">CONTACT US</a>
    </nav>
  </header>

  <section class="hero abs">
    <div class="hero-photo" role="img" aria-label="Photo of hands holding a smartphone showing a business report over printed charts"></div>
    <div class="hero-shade"></div>
    <div class="hero-copy">
      <h1 class="hero-title">HOW SOLID IS YOUR MARKETING DATA?</h1>
      <p class="hero-sub">CONVERT UNSTRUCTURED DATA INTO ACTIONABLE INTELLIGENCE</p>
      <a class="btn-solid" href="#">Read More</a>
    </div>
    <div class="hero-dots"><span class="is-active"></span><span></span><span></span><span></span></div>
  </section>

  <section class="welcome abs">
    <h2 class="welcome-title">WELCOME TO <em>PLOVTRIX</em></h2>
    <p class="welcome-text">We are a B2B Data, Analytics and Marketing Consulting Company specialized in harnessing the power of potential data to strengthen connections between decisions makers, companies and products. We focus on solutions engineered to solve distinct challenges in the data, direct marketing, and analytics space.</p>
    <a class="btn-outline" href="#">Read More</a>
  </section>

  <svg class="bands abs" width="1200" height="3141" aria-hidden="true">
    <polygon points="0,1334 1200,1407 1200,1644 0,1686" fill="var(--band)"/>
    <polygon points="0,2031 1200,2105 1200,2454 0,2387" fill="var(--band)"/>
  </svg>

  <section class="feature abs" style="left:75px;top:1060px;width:560px">
    <h2 class="feature-title">B2B Database</h2>
    <p class="feature-text">Get access to Asia’s leading market &amp; business intelligence database over 1,500,000 organizations and 3,500,000 decision makers.</p>
    <a class="btn-solid btn-plain" href="#">Read More</a>
  </section>
  <div class="art" style="left:722px;top:1047px;width:310px;height:251px;border-radius:10px;background:linear-gradient(135deg,#3f4a5f,#6c7a8f)" role="img" aria-label="Illustration of a server stack beside a laptop"></div>

  <div class="art" style="left:126px;top:1361px;width:303px;height:330px;border-radius:10px;background:linear-gradient(135deg,#e8ebf0,#d8474a)" role="img" aria-label="Illustration of a hand holding a magnifier over a target surrounded by marketing icons"></div>
  <section class="feature abs" style="left:526px;top:1447px;width:570px">
    <h2 class="feature-title light">Target Marketing</h2>
    <p class="feature-text light">We develop tailored marketing solutions based on your specific objectives, audience and budget to fetch high returns on investment.</p>
    <a class="btn-solid" href="#">Read More</a>
  </section>

  <section class="feature abs" style="left:75px;top:1772px;width:560px">
    <h2 class="feature-title">Call Centre</h2>
    <p class="feature-text">When your business requires instantaneous and cost effective contact center, we are here to provide the necessary expertise.</p>
    <a class="btn-solid btn-plain" href="#">Read More</a>
  </section>
  <div class="art" style="left:680px;top:1770px;width:430px;height:293px;border-radius:10px;background:linear-gradient(135deg,#f2e9df,#3a3f4a)" role="img" aria-label="Illustration of two call centre agents with headsets working at laptops"></div>

  <div class="art" style="left:136px;top:2094px;width:272px;height:283px;border-radius:10px;background:linear-gradient(135deg,#8fc2d9,#2f9fd6 55%,#f2a22b)" role="img" aria-label="Illustration of a cloud with a magnifier and data management icons"></div>
  <section class="feature abs" style="left:526px;top:2153px;width:570px">
    <h2 class="feature-title light">Data Management</h2>
    <p class="feature-text light">We analyze your data and report on effective strategies for turning the data into a profitable resource.</p>
    <a class="btn-solid" href="#">Read More</a>
  </section>

  <section class="feature abs" style="left:147px;top:2475px;width:430px">
    <h2 class="feature-title">Corporate Brochure</h2>
    <p class="feature-text" style="margin-top:18px">Learn our leading target marketing and intelligent data management solutions to attain new customers for your niche products and services.</p>
    <a class="btn-outline" href="#" style="margin-top:18px;padding:0 22px">Download Now</a>
  </section>
  <div class="art" style="left:643px;top:2456px;width:404px;height:245px;border-radius:6px;background:linear-gradient(135deg,#e6f2f5,#a9d3de)" role="img" aria-label="Illustration of two printed corporate brochures"></div>

  <footer class="site-footer abs">
    <div class="footer-col" style="left:75px;width:232px">
      <h3 class="footer-heading">About Plovtrix</h3>
      <p>Plovtrix is the primary source of market intelligence focused on identifying business opportunities and key decision makers throughout Asia Pacific Region. We provide access to over 3.5 million decision makers across 1.5 million profiled organizations in 23 Asia Pacific countries.</p>
    </div>
    <div class="footer-col" style="left:373px;width:180px">
      <h3 class="footer-heading">Quick Links</h3>
      <ul class="footer-list">
        <li>B2b Database</li><li>Call Centre</li><li>Demand Generation</li><li>Lead Generation</li><li>Data Management</li><li>Marketing Automation</li><li>Data Append</li><li>Event Management</li><li>Contact Us</li>
      </ul>
    </div>
    <div class="footer-col" style="left:588px;width:260px">
      <h3 class="footer-heading">Global HQ</h3>
      <div class="contact-row"><svg width="10" height="13" viewBox="0 0 10 13"><path d="M5 0a5 5 0 0 0-5 5c0 3.5 5 8 5 8s5-4.5 5-8a5 5 0 0 0-5-5zm0 7a2 2 0 1 1 0-4 2 2 0 0 1 0 4z" fill="#d6d6d6"/></svg><span>4810 Harlow Avenue, Suite 204, Bramfield, CA 90412-3300, USA</span></div>
      <div class="contact-row"><svg width="11" height="11" viewBox="0 0 11 11"><path d="M2 0l2 2.5-1 1.5a7 7 0 0 0 3.5 3.5l1.5-1L11 9l-1.5 2C4.5 11 0 6.5 0 1.5z" fill="#d6d6d6"/></svg><span>+1 (555) 014-2270</span></div>
      <div class="contact-row"><svg width="12" height="9" viewBox="0 0 12 9"><rect width="12" height="9" fill="#d6d6d6"/><path d="M0 0l6 5 6-5" stroke="#343434" fill="none"/></svg><span>contactus@plovtrix.com</span></div>
      <div class="contact-row"><svg width="11" height="11" viewBox="0 0 11 11"><circle cx="5.5" cy="5.5" r="5" fill="none" stroke="#d6d6d6" stroke-width="1.4"/><path d="M5.5 2.5v3h2.5" stroke="#d6d6d6" stroke-width="1.4" fill="none"/></svg><span>Monday – Friday : 9AM – 6PM</span></div>
    </div>
    <div class="footer-col" style="left:884px;width:250px">
      <h3 class="footer-heading">Regional HQ</h3>
      <div class="contact-row"><svg width="10" height="13" viewBox="0 0 10 13"><path d="M5 0a5 5 0 0 0-5 5c0 3.5 5 8 5 8s5-4.5 5-8a5 5 0 0 0-5-5zm0 7a2 2 0 1 1 0-4 2 2 0 0 1 0 4z" fill="#d6d6d6"/></svg><span>22 Tembra Road 3, #08-14 Kestrel Hub, Singapore 400000</span></div>
      <div class="contact-row"><svg width="11" height="11" viewBox="0 0 11 11"><path d="M2 0l2 2.5-1 1.5a7 7 0 0 0 3.5 3.5l1.5-1L11 9l-1.5 2C4.5 11 0 6.5 0 1.5z" fill="#d6d6d6"/></svg><span>+65 6000 4812</span></div>
      <div class="contact-row"><svg width="12" height="9" viewBox="0 0 12 9"><rect width="12" height="9" fill="#d6d6d6"/><path d="M0 0l6 5 6-5" stroke="#343434" fill="none"/></svg><span>contactus@plovtrix.com</span></div>
      <div class="contact-row"><svg width="11" height="11" viewBox="0 0 11 11"><circle cx="5.5" cy="5.5" r="5" fill="none" stroke="#d6d6d6" stroke-width="1.4"/><path d="M5.5 2.5v3h2.5" stroke="#d6d6d6" stroke-width="1.4" fill="none"/></svg><span>Monday – Friday : 9AM – 6PM</span></div>
    </div>
  </footer>

  <div class="footer-bar abs">
    <p class="copyright">Copyright © 2018. Company Name All Right Reserved</p>
    <div class="social" aria-label="Social media links"><span></span><span></span><span></span><span></span><span></span></div>
  </div>

</div>
</body>
</html>
```